Birchline Septic Solutions

Would like to see some single sided ones but would also like to see some double sided with one sided only being the logo. Owners name is Colin Vandro. Phone number is 555-214-0387
Services are pumping, inspections, installs, and repairs

Contact Information for Business Card

555-241-0387 Colin Vandro Maplecrest, OH

```html
<!DOCTYPE html>
<html lang="en">
<head>
<meta charset="utf-8">
<title>Birchline Septic Solutions – Business Card</title>
<link rel="stylesheet" href="https://fonts.googleapis.com/css2?family=Montserrat:wght@500;700&display=swap">
<style>
  :root {
    --page-bg: #e6e3e3;
    --card-light: #f3eded;
    --card-dark: #000000;
    --teal: #2bbcb8;
    --ink: #161616;
    --ink-soft: #2a2a2a;
  }
  * { margin: 0; padding: 0; box-sizing: border-box; }
  html, body {
    width: 1200px;
    height: 900px;
    overflow: hidden;
    background: var(--page-bg);
    font-family: "Montserrat", Arial, sans-serif;
  }
  .business-card {
    position: absolute;
    left: 100px;
    top: 140px;
    width: 1000px;
    height: 620px;
    background: var(--card-light);
    box-shadow: 0 14px 40px rgba(0,0,0,0.18);
    overflow: hidden;
  }
  .brand-panel {
    position: absolute;
    left: 0;
    top: 0;
    width: 507px;
    height: 556px;
    background: var(--card-light);
    display: flex;
    flex-direction: column;
    align-items: center;
    justify-content: center;
    padding-top: 24px;
    color: var(--ink);
    font-weight: 700;
  }
  .brand-name {
    font-size: 62px;
    line-height: 1;
    letter-spacing: 1px;
    text-transform: uppercase;
  }
  .brand-tagline {
    margin-top: 22px;
    font-size: 21px;
    letter-spacing: 7px;
    text-transform: uppercase;
    color: var(--ink);
  }
  .panel-divider {
    position: absolute;
    left: 507px;
    top: 0;
    width: 8px;
    height: 556px;
    background: var(--teal);
  }
  .contact-panel {
    position: absolute;
    left: 515px;
    top: 0;
    right: 0;
    height: 556px;
    background: var(--card-dark);
    padding: 218px 0 0 57px;
    color: var(--teal);
  }
  .owner-name {
    font-size: 40px;
    font-weight: 700;
    letter-spacing: 0.5px;
    text-transform: uppercase;
    margin-bottom: 50px;
  }
  .contact-line {
    display: flex;
    align-items: center;
    gap: 16px;
    font-size: 30px;
    font-weight: 500;
    letter-spacing: 1px;
    height: 46px;
  }
  .contact-icon {
    width: 26px;
    height: 30px;
    flex: none;
  }
  .services-band {
    position: absolute;
    left: 0;
    bottom: 0;
    width: 100%;
    height: 64px;
    background: var(--teal);
    display: flex;
    align-items: center;
    justify-content: center;
    gap: 10px;
    font-size: 29px;
    font-weight: 500;
    color: var(--ink);
    text-transform: uppercase;
    padding-right: 20px;
  }
  .service-dot {
    width: 13px;
    height: 13px;
    border-radius: 50%;
    background: #ffffff;
    display: inline-block;
  }
</style>
</head>
<body>
  <div class="business-card">
    <div class="brand-panel">
      <div class="brand-name">Birchline</div>
      <div class="brand-tagline">Septic Solutions</div>
    </div>

    <div class="panel-divider"></div>

    <div class="contact-panel">
      <div class="owner-name">Colin Vandro</div>
      <div class="contact-line">
        <svg class="contact-icon" viewBox="0 0 24 24" aria-hidden="true">
          <path fill="none" stroke="currentColor" stroke-width="2.2" stroke-linejoin="round"
            d="M5 3h4l2 5-2.5 1.5a11 11 0 0 0 6 6L16 13l5 2v4a2 2 0 0 1-2 2A16 16 0 0 1 3 5a2 2 0 0 1 2-2z"/>
          <path fill="none" stroke="currentColor" stroke-width="2" stroke-linecap="round" d="M15 3a6 6 0 0 1 6 6M15 7a2 2 0 0 1 2 2"/>
        </svg>
        <span class="contact-phone">555-214-0387</span>
      </div>
      <div class="contact-line">
        <svg class="contact-icon" viewBox="0 0 24 28" aria-hidden="true">
          <path fill="currentColor" fill-rule="evenodd"
            d="M12 1a10 10 0 0 1 10 10c0 7-10 16-10 16S2 18 2 11A10 10 0 0 1 12 1zm0 6a4 4 0 1 0 0 8 4 4 0 0 0 0-8z"/>
        </svg>
        <span class="contact-location">Maplecrest, OH</span>
      </div>
    </div>

    <div class="services-band">
      <span>Pumping</span><span class="service-dot"></span>
      <span>Inspections</span><span class="service-dot"></span>
      <span>Installs</span><span class="service-dot"></span>
      <span>Repairs</span>
    </div>
  </div>
</body>
</html>
```